Roadside building business signage for a holistic health clinic.

Replace signs as shown in the attached file. They are perforated stickers that go on the windows as shown. Looking for something that has our logo and says the name of the practice with logo (Fernridge Health & Wellness) also boldly says Acupuncture, IV Vitamins, and Holistic Health.
Possibly our phone number as well 318-562-7041
Updates

Please don't use pink except the logo. Earthy, organic tone colors appreciated.

Need of eye catching window signage of a holistic clinic on a brick building. Pink, purple, sage green, white color. Logo is pink on a white background. Please don't overload with too much pink. Words to include are "Fernridge Health and Wellness(name of business)", "Direct Primary Care", " Medical acupuncture", "IV Vitamin Therapy", "fernridgecareclinic.example","318-562-7041".

Target Market(s)

People will see in their cars passing by the building. Busy roadside so need to be visible while passing in fast speed.

Industry/Entity Type

Health & Wellness

Font styles to use
Sans Serif

Colors

Designer to choose colors to be used in the design.

Requirements
Must have
• On sign must have words Holistic Medicine, Medical Acupuncture, Direct Primary Care and IV vitamins.
Nice to have
• Simple, minimalistic, artistic yet has clear message. White, Black, Violet, Pink (logo), Dark green, Sage green.
Should not have
• Bold colors (red, yellow, blue), same tone colors. Blue waves on the current signage (uploaded file) must go.

```html
<!DOCTYPE html>
<html lang="en">
<head>
<meta charset="utf-8">
<title>Fernridge Health &amp; Wellness – Window Signage Panels</title>
<link href="https://fonts.googleapis.com/css2?family=Montserrat:wght@500;600;700&display=swap" rel="stylesheet">
<style>
  :root {
    --canvas: #ececec;
    --cream: #fbfaf5;
    --mist: #eef2ea;
    --sage-light: #dfe8d9;
    --sage: #9bb693;
    --sage-deep: #7f9c78;
    --violet: #6e4b8c;
    --violet-deep: #472c61;
    --forest: #0f5846;
    --logo-pink: #d2467f;
    --ink: #1f2a27;
    --rule: #a9b3a5;
    --white: #ffffff;
  }
  * { box-sizing: border-box; margin: 0; padding: 0; }
  html, body { width: 1200px; height: 2934px; overflow: hidden; }
  body {
    position: relative;
    background: var(--canvas);
    font-family: "Montserrat", Arial, sans-serif;
    color: var(--ink);
  }
  .panel {
    position: absolute;
    width: 540px;
    height: 540px;
    background:
      radial-gradient(circle at 78% 22%, var(--sage-light) 0%, rgba(223,232,217,0) 42%),
      radial-gradient(circle at 18% 78%, var(--mist) 0%, rgba(238,242,234,0) 48%),
      radial-gradient(circle at 30% 30%, var(--white) 0%, rgba(255,255,255,0) 35%),
      linear-gradient(160deg, var(--mist) 0%, var(--cream) 55%, var(--mist) 100%);
    box-shadow: 0 2px 6px rgba(0,0,0,0.12);
    overflow: hidden;
  }
  .panel svg.waves { position: absolute; inset: 0; width: 100%; height: 100%; }

  .panel--arch {
    left: 420px; top: 155px;
    clip-path: path("M0 0 C310 34 500 310 540 540 L0 540 Z");
    box-shadow: none;
  }
  .panel--brand { left: 40px; top: 850px; }
  .panel--services { left: 620px; top: 850px; }
  .panel--wave-a { left: 40px; top: 1545px; }
  .panel--wave-b { left: 620px; top: 1545px; }
  .panel--wave-c { left: 378px; top: 2240px; }

  /* brand panel */
  .brand-mark {
    position: absolute;
    left: 50%; top: 120px;
    width: 86px; height: 86px;
    margin-left: -43px;
    border-radius: 50%;
    background: var(--logo-pink);
  }
  .brand-name {
    position: absolute;
    left: 0; right: 0; top: 240px;
    text-align: center;
    font-weight: 600;
    font-size: 40px;
    line-height: 1.2;
    letter-spacing: 1px;
    color: var(--forest);
  }
  .brand-url {
    position: absolute;
    left: 0; right: 0; top: 448px;
    text-align: center;
    font-weight: 700;
    font-size: 19px;
    letter-spacing: 0.5px;
    color: var(--ink);
  }

  /* services panel */
  .foliage {
    position: absolute;
    left: 0; top: 0;
    width: 120px; height: 135px;
    background: radial-gradient(ellipse at 20% 20%, var(--sage) 0%, rgba(155,182,147,0.55) 45%, rgba(155,182,147,0) 72%);
  }
  .connectors { position: absolute; inset: 0; width: 100%; height: 100%; }
  .service-hex {
    position: absolute;
    width: 76px; height: 76px;
  }
  .service-label {
    position: absolute;
    width: 240px;
    font-weight: 700;
    font-size: 26px;
    line-height: 1.1;
    color: var(--ink);
  }
  .service-label--right { left: 272px; text-align: left; }
  .service-label--left { left: 12px; text-align: right; }
  .service-label--acupuncture { top: 46px; }
  .service-label--iv { top: 151px; }
  .service-label--holistic { top: 256px; }
  .service-label--primary { top: 361px; }
  .contact-bar {
    position: absolute;
    left: 0; right: 0; bottom: 0;
    height: 91px;
    background: var(--forest);
    border-top: 5px solid var(--sage);
    display: flex;
    align-items: center;
    justify-content: center;
    gap: 14px;
    color: var(--white);
  }
  .contact-bar svg { width: 24px; height: 24px; flex: none; }
  .contact-phone { font-weight: 700; font-size: 30px; letter-spacing: 0.5px; }
  .contact-url { font-weight: 600; font-size: 18px; }
  .contact-item { display: flex; align-items: center; gap: 6px; }
</style>
</head>
<body>

  <!-- arched top pane -->
  <div class="panel panel--arch">
    <svg class="waves" viewBox="0 0 310 312" preserveAspectRatio="none">
      <linearGradient id="archBand" x1="0" y1="0" x2="0" y2="1">
        <stop offset="0" stop-color="var(--violet)"/><stop offset="1" stop-color="var(--violet-deep)"/>
      </linearGradient>
      <path d="M0 88 C40 90 60 140 100 175 C140 205 200 205 255 200 L262 210 C200 218 130 218 90 188 C55 160 40 120 0 110 Z" fill="var(--forest)"/>
      <path d="M0 96 C35 92 55 150 95 190 C130 222 200 226 285 222 L292 240 C200 242 120 240 80 208 C45 178 30 122 0 118 Z" fill="var(--white)"/>
      <path d="M0 102 C35 100 55 158 95 196 C130 228 200 230 288 230 L295 250 C200 252 115 250 75 214 C40 182 28 130 0 126 Z" fill="url(#archBand)"/>
    </svg>
  </div>

  <!-- brand pane -->
  <div class="panel panel--brand">
    <div class="brand-mark"></div>
    <div class="brand-name">Fernridge<br>Health &amp; Wellness</div>
    <div class="brand-url">www.fernridgecareclinic.example</div>
  </div>

  <!-- services pane -->
  <div class="panel panel--services">
    <div class="foliage" role="img" aria-label="Trailing eucalyptus sprig in sage green"></div>
    <svg class="connectors" viewBox="0 0 540 540">
      <polyline points="239,45 262,28 520,28" fill="none" stroke="var(--rule)" stroke-width="1.5"/>
      <polyline points="239,121 262,138 520,138" fill="none" stroke="var(--rule)" stroke-width="1.5"/>
      <polyline points="279,150 256,133 20,133" fill="none" stroke="var(--rule)" stroke-width="1.5"/>
      <polyline points="279,226 256,243 20,243" fill="none" stroke="var(--rule)" stroke-width="1.5"/>
      <polyline points="239,255 262,238 520,238" fill="none" stroke="var(--rule)" stroke-width="1.5"/>
      <polyline points="239,331 262,348 520,348" fill="none" stroke="var(--rule)" stroke-width="1.5"/>
      <polyline points="279,360 256,343 20,343" fill="none" stroke="var(--rule)" stroke-width="1.5"/>
      <polyline points="279,436 256,440 20,440" fill="none" stroke="var(--rule)" stroke-width="1.5"/>
    </svg>
    <svg class="service-hex" style="left:180px;top:45px" viewBox="0 0 92 92" role="img" aria-label="Meditation icon for medical acupuncture">
      <polygon points="46,2 84,24 84,68 46,90 8,68 8,24" fill="var(--violet)" stroke="var(--white)" stroke-width="3"/>
      <polygon points="46,12 75,29 75,63 46,80 17,63 17,29" fill="none" stroke="var(--white)" stroke-width="1.5"/>
    </svg>
    <svg class="service-hex" style="left:262px;top:150px" viewBox="0 0 92 92" role="img" aria-label="IV drip bag icon">
      <polygon points="46,2 84,24 84,68 46,90 8,68 8,24" fill="var(--forest)" stroke="var(--white)" stroke-width="3"/>
      <polygon points="46,12 75,29 75,63 46,80 17,63 17,29" fill="none" stroke="var(--white)" stroke-width="1.5"/>
    </svg>
    <svg class="service-hex" style="left:180px;top:255px" viewBox="0 0 92 92" role="img" aria-label="Hand holding a leaf icon for holistic medicine">
      <polygon points="46,2 84,24 84,68 46,90 8,68 8,24" fill="var(--violet)" stroke="var(--white)" stroke-width="3"/>
      <polygon points="46,12 75,29 75,63 46,80 17,63 17,29" fill="none" stroke="var(--white)" stroke-width="1.5"/>
    </svg>
    <svg class="service-hex" style="left:262px;top:360px" viewBox="0 0 92 92" role="img" aria-label="Stethoscope icon for direct primary care">
      <polygon points="46,2 84,24 84,68 46,90 8,68 8,24" fill="var(--forest)" stroke="var(--white)" stroke-width="3"/>
      <polygon points="46,12 75,29 75,63 46,80 17,63 17,29" fill="none" stroke="var(--white)" stroke-width="1.5"/>
    </svg>
    <div class="service-label service-label--right service-label--acupuncture">Medical<br>Acupuncture</div>
    <div class="service-label service-label--left service-label--iv">IV Vitamin<br>Therapy</div>
    <div class="service-label service-label--right service-label--holistic">Holistic<br>Medicine</div>
    <div class="service-label service-label--left service-label--primary">Direct<br>Primary Care</div>
    <div class="contact-bar">
      <span class="contact-item">
        <svg viewBox="0 0 24 24"><path d="M6.6 10.8a15.1 15.1 0 0 0 6.6 6.6l2.2-2.2a1 1 0 0 1 1-.25 11.4 11.4 0 0 0 3.6.57 1 1 0 0 1 1 1V20a1 1 0 0 1-1 1A17 17 0 0 1 3 4a1 1 0 0 1 1-1h3.5a1 1 0 0 1 1 1c0 1.25.2 2.45.57 3.6a1 1 0 0 1-.25 1z" fill="var(--sage)"/></svg>
        <span class="contact-phone">318-562-7041</span>
      </span>
      <span class="contact-item">
        <svg viewBox="0 0 24 24" style="width:18px;height:18px"><circle cx="12" cy="12" r="9" fill="none" stroke="var(--sage)" stroke-width="2"/><ellipse cx="12" cy="12" rx="4" ry="9" fill="none" stroke="var(--sage)" stroke-width="2"/><line x1="3" y1="12" x2="21" y2="12" stroke="var(--sage)" stroke-width="2"/></svg>
        <span class="contact-url">fernridgecareclinic.example</span>
      </span>
    </div>
  </div>

  <!-- wave pane A -->
  <div class="panel panel--wave-a">
    <svg class="waves" viewBox="0 0 313 313" preserveAspectRatio="none">
      <linearGradient id="bandA" x1="0" y1="0" x2="0" y2="1">
        <stop offset="0" stop-color="var(--violet)"/><stop offset="1" stop-color="var(--violet-deep)"/>
      </linearGradient>
      <path d="M0 50 C40 80 90 108 150 114 L150 118 C90 116 40 98 0 78 Z" fill="var(--forest)"/>
      <path d="M0 78 C45 100 95 118 160 116 C225 114 275 124 313 138 L313 205 C260 196 210 192 160 204 C110 214 55 200 0 186 Z" fill="url(#bandA)"/>
      <path d="M150 200 C220 188 280 212 313 262 L313 282 C280 232 225 206 155 206 Z" fill="var(--white)"/>
      <path d="M150 204 C225 192 285 220 313 270 L313 252 C285 208 225 186 150 200 Z" fill="var(--forest)"/>
    </svg>
  </div>

  <!-- wave pane B -->
  <div class="panel panel--wave-b">
    <svg class="waves" viewBox="0 0 313 313" preserveAspectRatio="none">
      <linearGradient id="bandB" x1="0" y1="0" x2="0" y2="1">
        <stop offset="0" stop-color="var(--violet)"/><stop offset="1" stop-color="var(--violet-deep)"/>
      </linearGradient>
      <path d="M18 90 C90 70 170 76 230 95 C260 104 290 94 313 76 L313 130 C280 120 240 112 200 104 C140 92 80 86 18 90 Z" fill="var(--forest)"/>
      <path d="M18 90 C80 84 140 90 200 102 C240 110 280 118 313 130 L313 134 C270 124 230 116 190 110 C130 100 70 94 18 92 Z" fill="var(--white)"/>
      <path d="M0 104 C40 94 80 96 130 104 C200 114 260 126 313 136 L313 225 C260 222 200 205 130 196 C80 190 40 196 0 212 Z" fill="url(#bandB)"/>
    </svg>
  </div>

  <!-- wave pane C -->
  <div class="panel panel--wave-c">
    <svg class="waves" viewBox="0 0 313 313" preserveAspectRatio="none">
      <linearGradient id="bandC" x1="0" y1="0" x2="0" y2="1">
        <stop offset="0" stop-color="var(--violet)"/><stop offset="1" stop-color="var(--violet-deep)"/>
      </linearGradient>
      <path d="M170 140 C230 138 280 118 313 84 L313 110 C285 138 240 150 175 146 Z" fill="var(--forest)"/>
      <path d="M170 144 C235 144 282 124 313 100 L313 108 C282 132 235 152 170 150 Z" fill="var(--white)"/>
      <path d="M0 112 C40 96 90 92 140 102 C200 116 260 146 313 150 L313 222 C260 220 210 206 160 196 C100 186 50 196 0 214 Z" fill="url(#bandC)"/>
      <path d="M0 236 C40 196 100 182 150 196 C100 190 50 206 0 250 Z" fill="var(--forest)"/>
      <path d="M0 226 C45 194 100 182 150 194 L150 198 C100 188 45 200 0 234 Z" fill="var(--white)"/>
    </svg>
  </div>

</body>
</html>
```